New Business Card for Web Design/Internet Marketing Company

Looking for a great looking new business card. We are a 10 year old web design, internet marketing and website management company that works mostly with small businesses.

Our new card needs to better match the colors and style of our website, be bold, extremely usable and slightly edgy.

Target Market(s)

Small/Medium businesses that have websites

Industry/Entity Type

Internet

Requirements
Must have
• Front and back design, full color, rounded corners please

Must use the colors/style of our website (JPG provided)

INFO FOR CARDS (as readable as possible please)
Mark Lenner
President/CEO
mark@trelvanmedia.example
Phone: 520-381-7459
Toll Free: 866-381-7459
Address: 4315 W. Calloway Ave. Ste. 140, Tucson, AZ 85792

THINGS I WANT TO PROMOTE (if there is room):
1. Our Website - www.trelvanmedia.example

2. Social Media
Twitter: @trelvanmedia
Facebook: www.facebook.com/trelvanmedia

3. Our Services
Web Design
Internet Marketing
Website Management

```html
<!DOCTYPE html>
<html lang="en">
<head>
<meta charset="utf-8">
<title>Trelvan Media – Business Card</title>
<link href="https://fonts.googleapis.com/css2?family=Open+Sans:wght@400;600;700;800&display=swap" rel="stylesheet">
<style>
  :root {
    --bg: #ece9e4;
    --card-white: #ffffff;
    --card-gray: #5e5e5f;
    --brand-blue: #1a8ccf;
    --brand-orange: #f58a2a;
    --text-gray: #555555;
    --rule-gray: #9a9a9a;
    --white: #ffffff;
  }
  * { box-sizing: border-box; margin: 0; padding: 0; }
  html, body { width: 1200px; height: 402px; overflow: hidden; }
  body {
    background: var(--bg);
    font-family: "Open Sans", Arial, sans-serif;
    position: relative;
  }
  .card {
    position: absolute;
    top: 57px;
    height: 292px;
    border-radius: 10px;
    overflow: hidden;
    box-shadow: 0 2px 8px rgba(0,0,0,.18);
  }
  .card--front { left: 61px; width: 544px; background: var(--card-white); }
  .card--back  { left: 626px; width: 512px; background: var(--card-gray); color: var(--white); text-align: center; }

  /* front */
  .brand {
    position: absolute; left: 70px; top: 48px;
    display: flex; align-items: center; gap: 12px;
  }
  .brand__dot { width: 34px; height: 34px; border-radius: 50%; background: var(--brand-orange); }
  .brand__name { font-size: 40px; font-weight: 800; color: var(--brand-blue); letter-spacing: -1px; line-height: 1; }
  .tagline {
    position: absolute; right: 66px; top: 98px;
    font-size: 15px; color: var(--text-gray);
  }
  .details { position: absolute; top: 150px; font-size: 12.5px; color: var(--text-gray); line-height: 18px; }
  .details--social { right: 293px; text-align: right; }
  .details--social .gap { height: 12px; }
  .details--contact { left: 288px; }
  .details li { list-style: none; display: flex; align-items: center; gap: 5px; }
  .details--social li { justify-content: flex-end; }
  .icon { width: 10px; height: 10px; flex: none; }
  .divider { position: absolute; left: 268px; top: 150px; width: 1px; height: 80px; background: var(--rule-gray); }
  .bands { position: absolute; left: 0; bottom: 0; width: 544px; height: 50px; }
  .signature {
    position: absolute; left: 282px; bottom: 14px;
    color: var(--white); font-size: 16px; font-weight: 700;
  }
  .signature__title { font-size: 12px; font-weight: 400; }

  /* back */
  .back__name { margin-top: 72px; font-size: 40px; font-weight: 800; color: var(--brand-orange); letter-spacing: -1px; }
  .services__heading {
    display: inline-block; margin-top: 40px; padding: 0 14px 3px;
    font-size: 21px; font-weight: 600; border-bottom: 2px solid var(--white);
  }
  .services__list { margin-top: 12px; font-size: 17.5px; line-height: 26px; }
</style>
</head>
<body>
  <section class="card card--front">
    <div class="brand">
      <span class="brand__dot"></span>
      <span class="brand__name">Trelvan Media</span>
    </div>
    <p class="tagline">Grow your Business</p>

    <ul class="details details--social">
      <li><svg class="icon" viewBox="0 0 10 10"><rect width="10" height="10" rx="1.5" fill="var(--brand-blue)"/></svg>trelvanmedia</li>
      <li><svg class="icon" viewBox="0 0 10 10"><rect width="10" height="10" rx="1.5" fill="var(--brand-blue)"/></svg>@trelvanmedia</li>
      <li class="gap"></li>
      <li>4315 W. Calloway Ave. Ste. 140</li>
      <li>Tucson, AZ 85792</li>
    </ul>
    <div class="divider"></div>
    <ul class="details details--contact">
      <li><svg class="icon" viewBox="0 0 10 10"><circle cx="5" cy="5" r="5" fill="var(--brand-blue)"/><path d="M3 2.5l1.3 1.3-.6.8c.4.8 1 1.4 1.8 1.8l.8-.6L7.5 7 6.8 7.8C4.8 7.6 2.4 5.2 2.2 3.2z" fill="#fff"/></svg>520-381-7459</li>
      <li><svg class="icon" viewBox="0 0 10 10"><circle cx="5" cy="5" r="5" fill="var(--brand-blue)"/><path d="M3 2.5l1.3 1.3-.6.8c.4.8 1 1.4 1.8 1.8l.8-.6L7.5 7 6.8 7.8C4.8 7.6 2.4 5.2 2.2 3.2z" fill="#fff"/></svg>866-381-7459</li>
      <li><svg class="icon" viewBox="0 0 10 10"><rect y="2" width="10" height="6.5" fill="var(--brand-blue)"/><path d="M0 2l5 3.5L10 2" stroke="#fff" stroke-width="1" fill="none"/></svg>mark@trelvanmedia.example</li>
      <li><svg class="icon" viewBox="0 0 10 10"><circle cx="5" cy="5" r="4.5" fill="var(--brand-blue)"/><path d="M.5 5h9M5 .5v9" stroke="#fff" stroke-width=".8"/><ellipse cx="5" cy="5" rx="2" ry="4.5" stroke="#fff" stroke-width=".8" fill="none"/></svg>www.trelvanmedia.example</li>
    </ul>

    <svg class="bands" viewBox="0 0 544 50" aria-hidden="true">
      <polygon points="0,24 182,24 170,50 0,50" fill="var(--brand-blue)"/>
      <polygon points="210,0 544,0 544,50 186,50" fill="var(--card-gray)"/>
    </svg>
    <p class="signature">Mark Lenner, <span class="signature__title">President/CEO</span></p>
  </section>

  <section class="card card--back">
    <p class="back__name">Trelvan Media</p>
    <h2 class="services__heading">Our Services</h2>
    <p class="services__list">Web Design &nbsp;•&nbsp; Internet Marketing<br>Website Management</p>
  </section>
</body>
</html>
```